Business Card Design Project

I need a business card design for an Organic drive thru coffee kiosk. We will serve organic coffee, teas & smoothies and will serve healthy breakfast food/snacks for people on the go.
I want the card to have 2-3 colors max (earthy colors like browns, greens and so on).
I have attached the logo I want used and would love to play off the theme of "balance."
Include:
Sun-Leaf Coffee
address: 3712 Pelwin Ct. Raleigh, NC 27699
phone: 919-555-0143
website: www.sun-leaf.com (website is not up yet but still include it on card)
email: Dorothy@sun-leaf.com
I want one of the following sayings somewhere on the card (the front or back is fine):
"Eat & Drink Well, on the run!"
"Break the fast with Sun-Leaf"
Maybe on the back list what we offer:
-Organic coffee, espresso & tea
-Blendora smoothies & protein shakes
-Zippy Tonic (100% fresh local fruit and veggies)
-Vital Nibbles
College age to 55
Business

```html
<!DOCTYPE html>
<html lang="en">
<head>
<meta charset="utf-8">
<title>Sun-Leaf Coffee – Business Cards</title>
<link rel="stylesheet" href="https://fonts.googleapis.com/css2?family=Ubuntu:wght@400;500;700&display=swap">
<style>
  :root {
    --backdrop: #efece4;
    --card-brown: #7a5535;
    --ink-brown: #4e3526;
    --mark-brown: #8d4e3c;
    --leaf-green: #8cc461;
    --band-green: #4b6a2f;
    --tan: #c9a070;
  }
  * { margin: 0; padding: 0; box-sizing: border-box; }
  html, body {
    width: 1200px; height: 900px; overflow: hidden;
    background: var(--backdrop);
    font-family: "Ubuntu", sans-serif;
  }
  .canvas { position: relative; width: 1200px; height: 900px; }
  .card {
    position: absolute; top: 71px;
    width: 439px; height: 767px;
    background: var(--card-brown);
    box-shadow: 9px 12px 12px rgba(0,0,0,0.35);
    text-align: center;
    overflow: hidden;
  }
  .card--back { left: 130px; }
  .card--front { left: 661px; }
  .line { position: absolute; left: 0; width: 100%; }

  /* back */
  .brand-mark {
    position: absolute; left: 50%; top: 214px; transform: translateX(-50%);
    display: flex; align-items: center; gap: 14px;
  }
  .brand-mark__dot { width: 64px; height: 64px; border-radius: 50%; background: var(--mark-brown); }
  .brand-mark__name { font-size: 58px; font-weight: 500; color: var(--ink-brown); white-space: nowrap; }
  .offerings { list-style: none; }
  .offerings li {
    position: absolute; left: 0; width: 100%;
    font-size: 17px; color: var(--leaf-green);
  }
  .website { top: 790px; font-size: 21px; color: var(--tan); top: 788px; }
  .card--back .website { top: 717px; }

  /* front */
  .person { top: 36px; font-size: 24px; font-weight: 700; color: var(--leaf-green); }
  .logo {
    position: absolute; left: 50%; top: 150px; transform: translateX(-50%);
    display: flex; align-items: center; gap: 12px;
  }
  .logo__dot { width: 48px; height: 48px; border-radius: 50%; background: var(--mark-brown); }
  .logo__name { font-size: 62px; font-weight: 500; color: var(--ink-brown); white-space: nowrap; }
  .subline { top: 250px; font-size: 15px; font-weight: 700; letter-spacing: 3px; color: var(--leaf-green); }
  .company { top: 376px; font-size: 30px; font-weight: 700; color: var(--leaf-green); }
  .contact { font-size: 17px; color: var(--tan); line-height: 21px; }
  .address { top: 533px; }
  .reach { top: 620px; }
  .slogan-band {
    position: absolute; left: 0; bottom: 0; width: 100%; height: 69px;
    background: var(--band-green);
    color: var(--leaf-green); font-size: 17px; line-height: 20px;
    padding-top: 10px;
  }
</style>
</head>
<body>
<main class="canvas">
  <section class="card card--back" aria-label="Card back">
    <div class="brand-mark">
      <span class="brand-mark__dot"></span>
      <span class="brand-mark__name">Sun-Leaf</span>
    </div>
    <ul class="offerings">
      <li style="top:454px">Organic Coffee, espresso &amp; tea</li>
      <li style="top:498px">Blendora smoothies &amp; protein shakes</li>
      <li style="top:542px">Zippy Tonic (100% local fruit &amp; veggies)</li>
      <li style="top:587px">Vital Nibbles</li>
    </ul>
    <p class="line website">www.sun-leaf.com</p>
  </section>

  <section class="card card--front" aria-label="Card front">
    <p class="line person">Dorothy</p>
    <div class="logo">
      <span class="logo__dot"></span>
      <span class="logo__name">Sun-Leaf</span>
    </div>
    <p class="line subline">ORGANIC COFFEE + CAFE</p>
    <h1 class="line company">Sun-Leaf Coffee</h1>
    <p class="line contact address">3712 Pelwin Ct. Raleigh<br>NC 27699</p>
    <p class="line contact reach">919-555-0143<br>Dorothy@sun-leaf.com</p>
    <p class="slogan-band">Eat and drink well, on the run !.<br>Break the fast, with Sun-Leaf</p>
  </section>
</main>
</body>
</html>
```